Frostvale Harborline LLC

we need a business card design

Industry/Entity Type

hvac

Contact Information for Business Card

my logo

Requirements
Must have
• my logo and same colors

```html
<!DOCTYPE html>
<html lang="en">
<head>
<meta charset="utf-8">
<title>Frostvale Harborline LLC — Business Card</title>
<link href="https://fonts.googleapis.com/css2?family=Montserrat:wght@400;500;700;800&display=swap" rel="stylesheet">
<style>
  :root {
    --bg: #2b2b2b;
    --brand-blue: #1b63b0;
    --brand-blue-dark: #0f4f99;
    --brand-gold: #f3a93a;
    --card-white: #ffffff;
    --ink: #1f1f1f;
    --rule: #1b63b0;
  }
  * { box-sizing: border-box; margin: 0; padding: 0; }
  html, body {
    width: 1200px; height: 875px; overflow: hidden;
    background: var(--bg);
    font-family: "Montserrat", sans-serif;
  }
  .stage {
    width: 1200px; height: 875px;
    display: flex; align-items: center; justify-content: center; gap: 40px;
  }
  .card {
    width: 540px; height: 310px;
    border-radius: 22px;
    position: relative; overflow: hidden;
  }
  .card-front {
    background: var(--brand-blue);
    display: flex; align-items: center; justify-content: center;
  }
  .front-pattern {
    position: absolute; inset: 0;
    background: linear-gradient(135deg, var(--brand-blue) 0%, var(--brand-blue-dark) 100%);
  }
  .brand-mark {
    position: relative;
    display: flex; align-items: center; gap: 12px;
  }
  .brand-dot {
    width: 22px; height: 22px; border-radius: 50%;
    background: var(--brand-gold);
    flex: none;
  }
  .brand-name {
    font-weight: 800; font-size: 30px; line-height: 1.1;
    color: var(--card-white);
    text-transform: uppercase; letter-spacing: 0.5px;
  }
  .card-back { background: var(--card-white); }
  .card-back .brand-mark {
    position: absolute; left: 50%; top: 78px; transform: translateX(-50%);
  }
  .card-back .brand-name { color: var(--brand-blue); font-size: 26px; white-space: nowrap; }
  .card-details {
    position: absolute; left: 0; right: 0; top: 170px;
    display: flex; justify-content: center; align-items: center; gap: 16px;
  }
  .person { text-align: right; }
  .person-name { font-weight: 700; font-size: 22px; color: var(--brand-blue-dark); }
  .person-title { font-size: 12px; color: var(--ink); margin-top: 2px; }
  .divider { width: 2px; height: 74px; background: var(--rule); }
  .contact-list { list-style: none; display: flex; flex-direction: column; gap: 7px; }
  .contact-item { display: flex; align-items: center; gap: 8px; font-size: 12px; color: var(--ink); }
  .contact-icon { width: 13px; height: 13px; flex: none; }
</style>
</head>
<body>
<main class="stage">
  <section class="card card-front" aria-label="Card front">
    <div class="front-pattern" role="img" aria-label="Faint repeated brand pattern on blue"></div>
    <div class="brand-mark">
      <span class="brand-dot"></span>
      <span class="brand-name">Frostvale Harborline LLC</span>
    </div>
  </section>

  <section class="card card-back" aria-label="Card back">
    <div class="brand-mark">
      <span class="brand-dot"></span>
      <span class="brand-name">Frostvale Harborline LLC</span>
    </div>
    <div class="card-details">
      <div class="person">
        <p class="person-name">Darren Okafor</p>
        <p class="person-title">Managing Director</p>
      </div>
      <div class="divider"></div>
      <ul class="contact-list">
        <li class="contact-item">
          <svg class="contact-icon" viewBox="0 0 14 14"><rect x="3" y="0.8" width="8" height="12.4" rx="1.5" fill="none" stroke="var(--brand-gold)" stroke-width="1.4"/><circle cx="7" cy="11" r="0.8" fill="var(--brand-gold)"/></svg>
          +1 (555) 014-2298
        </li>
        <li class="contact-item">
          <svg class="contact-icon" viewBox="0 0 14 14"><rect x="0.5" y="2.5" width="13" height="9" rx="1" fill="var(--brand-gold)"/><path d="M1 3.2 L7 8 L13 3.2" fill="none" stroke="#fff" stroke-width="1.2"/></svg>
          hello@frostvaleharbor.com
        </li>
        <li class="contact-item">
          <svg class="contact-icon" viewBox="0 0 14 14"><circle cx="7" cy="7" r="6" fill="var(--brand-gold)"/><path d="M1 7 H13 M7 1 C4 4 4 10 7 13 M7 1 C10 4 10 10 7 13" fill="none" stroke="#fff" stroke-width="0.9"/></svg>
          www.frostvaleharbor.com
        </li>
      </ul>
    </div>
  </section>
</main>
</body>
</html>
```